Home Security Company Business Card

Looking for a eye catching business card that is non traditional and stands out but yet still looks professional. It should include all the pertinent information such as name, title, address, telephone, e-mail, website address should definitely stand out and then finally the logo.

Target Market(s)

Residential and Commercial accounts mostly upscale accounts

Industry/Entity Type

Security

Contact Information for Business Card

Name
Title
Address
Office #
Cell #
E-mail
Website

Font styles to use
Serif
Sans Serif

Requirements
Must have
• Logo, two sided color configuration
Nice to have
• You decide
Should not have
• There really aren't any.

```html
<!DOCTYPE html>
<html lang="en">
<head>
<meta charset="utf-8">
<title>Ironvale Security Group — Business Card</title>
<link rel="stylesheet" href="https://fonts.googleapis.com/css2?family=Open+Sans:wght@400;600;700&display=swap">
<style>
  :root {
    --stage: #e9e4de;
    --wine-light: #b3323f;
    --wine: #8e1c28;
    --wine-dark: #5e0f18;
    --gold-light: #fbe08a;
    --gold: #eec04e;
    --gold-dark: #d69d2a;
    --paper: #ffffff;
    --ink-white: #ffffff;
  }
  * { box-sizing: border-box; margin: 0; padding: 0; }
  html, body { width: 1200px; height: 913px; overflow: hidden; }
  body {
    background: var(--stage);
    font-family: "Open Sans", Arial, sans-serif;
    position: relative;
  }
  .card {
    position: absolute;
    width: 520px;
    height: 298px;
    border-radius: 14px;
    overflow: hidden;
    box-shadow: 0 10px 24px rgba(0,0,0,0.25);
  }
  /* Front */
  .card--front {
    left: 50px; top: 308px;
    background: linear-gradient(135deg, var(--wine-light) 0%, var(--wine) 45%, var(--wine-dark) 100%);
  }
  .front__band {
    position: absolute; left: 0; top: 0; bottom: 0; width: 34px;
    background: linear-gradient(90deg, var(--gold-light), var(--gold) 60%, var(--gold-dark));
  }
  .front__icons {
    position: absolute; left: 0; width: 34px; bottom: 26px;
    display: flex; flex-direction: column; align-items: center; gap: 7px;
  }
  .front__icons svg { width: 13px; height: 13px; fill: var(--wine-dark); }
  .brand {
    display: flex; align-items: center; gap: 8px;
    font-weight: 700; letter-spacing: 0.04em; text-transform: uppercase;
  }
  .brand__dot { border-radius: 50%; background: var(--gold); }
  .front__brand { position: absolute; left: 60px; top: 38px; color: var(--ink-white); font-size: 15px; }
  .front__brand .brand__dot { width: 22px; height: 22px; }
  .front__details {
    position: absolute; left: 60px; top: 118px; color: var(--ink-white);
  }
  .person__name { font-size: 26px; font-weight: 700; line-height: 1.1; }
  .person__title { color: var(--gold); font-size: 14px; font-weight: 600; margin-bottom: 10px; }
  .contact { list-style: none; font-size: 14.5px; line-height: 1.28; }
  /* Back */
  .card--back {
    left: 630px; top: 308px;
    background: var(--paper);
  }
  .back__band {
    position: absolute; right: 0; top: 0; bottom: 0; width: 40px;
    background: linear-gradient(90deg, var(--gold-dark), var(--gold) 40%, var(--gold-light));
  }
  .back__brand {
    position: absolute; left: 0; right: 40px; top: 110px;
    justify-content: center; color: var(--wine); font-size: 22px;
  }
  .back__brand .brand__dot { width: 30px; height: 30px; }
  .back__web {
    position: absolute; left: 0; right: 40px; top: 205px; text-align: center;
    color: var(--wine); font-size: 16px; font-weight: 700;
  }
</style>
</head>
<body>
  <section class="card card--front" aria-label="Business card front">
    <div class="front__band">
      <div class="front__icons">
        <svg viewBox="0 0 24 24" aria-label="Office phone"><path d="M4 8c0-2 2-4 8-4s8 2 8 4v2h-4V8H8v2H4z M6 12h12l2 8H4z"/></svg>
        <svg viewBox="0 0 24 24" aria-label="Mobile phone"><path d="M6 2l4 0 2 5-3 2c1 3 3 5 6 6l2-3 5 2v4c0 1-1 2-2 2C10 20 4 14 4 4c0-1 1-2 2-2z"/></svg>
        <svg viewBox="0 0 24 24" aria-label="Email"><path d="M2 5h20v14H2z M3 6l9 7 9-7" fill="none" stroke="#5e0f18" stroke-width="2"/></svg>
        <svg viewBox="0 0 24 24" aria-label="Address"><path d="M12 2a7 7 0 0 1 7 7c0 5-7 13-7 13S5 14 5 9a7 7 0 0 1 7-7zm0 4a3 3 0 1 0 0 6 3 3 0 0 0 0-6z"/></svg>
      </div>
    </div>
    <div class="brand front__brand"><span class="brand__dot"></span>Ironvale Security Group</div>
    <div class="front__details">
      <h1 class="person__name">Daniel Harrow</h1>
      <p class="person__title">Owner</p>
      <ul class="contact">
        <li>+555 0148-2731</li>
        <li>+5550193-46208</li>
        <li>hello@danielharrowmail.com</li>
        <li>742 Alder Lane Brookfield, Ohio 44012</li>
      </ul>
    </div>
  </section>

  <section class="card card--back" aria-label="Business card back">
    <div class="brand back__brand"><span class="brand__dot"></span>Ironvale Security Group</div>
    <p class="back__web">www.ironvalesecuritygroup.com</p>
    <div class="back__band"></div>
  </section>
</body>
</html>
```